San Francisco Leading Consulting firm - 47Vora Web Design Project

•Create a Web Design
•Uncoded webpage layout design
•2 Pages Design - Homepage + Interior Page

Task Description
Hello, we're looking for a re-design our current website www.47vora-example.com

we have a sample mockup design @

http://47vora.pubtrellis-example.org/

This shows the layout that we like and also a sample of 6 pictures that would change based on where you mouse over..

6 pictures HOME design needs to be included.

SMART
THOUGHTFUL
FLEXIBLE
CREATIVE SERVICES
TECHNICAL SERVICES
PARTNERS

sites we like:

http://www.melvanadvisory-example.com/Home.cfm?id=Home
http://www.plinthworks-example.com/index.html

Our company can be best described as: 100+ employees, cutting-edge, depandable, innovative, strong, smart.

Our Primary focus is: IT Consulting Services and Creative Design services

47Vora LLC is a consulting firm providing creative design, business and technology solutions to both private and public interests.

Established in 1996, 47Vora is a San Francisco based company providing specialists for a range of business needs including:

Creative Design Services
•Print
•Logo Design
•Website Design
•Illustration

and

Business and Technology solutions

•Application Software and Web Development
•Business Process Re-Design (BPR)
•Business/Systems Analysis and Requirement Documentation
•Mentoring and Training
•Network/Hardware Installation Services
•System Design and Architecture
•Vendor Management
•Docuvault Architecture and Implementation

our sample mockup site:

Reason: Due to holiday season, we're not available to work with designers and finilize our design.  

Thank you very much for submitting your design.

We appreciate your time and creativity.   Since, our office is currently closed for holidays, we will be reviewing it in details next week and will make our decision as soon as possible.

It would be great if you could submit any of your changes by Wed next week, so it would be part of our reviews. 

Please see updated wireframe under attachments:  we have some minor updates to our wireframe that we would like you to update your designs, if possible.  

We also encorouge you not to use our standard wireframe and come up with more unique designs.   Everything would be considered when we review your design.

 

Target Market(s)

Creative services and professional services clients, including government agencies

Industry/Entity Type

Business

Requirements
Must have
• Clean, professional look, easy navigation

```html
<!DOCTYPE html>
<html lang="en">
<head>
<meta charset="utf-8">
<title>47Vora — Home</title>
<link rel="stylesheet" href="https://fonts.googleapis.com/css2?family=Roboto+Condensed:wght@400;700&family=Arimo:wght@400;700&display=swap">
<style>
  :root {
    --blue: #2b8bcb;
    --blue-pale: #e8f4fb;
    --line: #dfe9f0;
    --frame: #e9eff4;
    --text: #555b60;
    --title: #5f6266;
    --olive: #7f9412;
    --olive-dark: #5f7009;
    --footer-bg: #eeeff2;
    --board: #3b3f32;
    --board-dark: #23271f;
  }
  * { box-sizing: border-box; margin: 0; padding: 0; }
  html, body { width: 1200px; height: 640px; overflow: hidden; }
  body {
    position: relative;
    background: linear-gradient(to bottom, #fff 0, #fff 590px, var(--footer-bg) 590px);
    font-family: "Arimo", Arial, sans-serif;
    color: var(--text);
  }
  .sheet {
    position: absolute; left: 216px; top: 0; width: 760px; height: 590px;
    background: #fff; border-radius: 0 0 8px 0;
  }
  .brand {
    position: absolute; left: 224px; top: 22px;
    display: flex; align-items: center; gap: 8px;
    font-family: "Roboto Condensed", Arial, sans-serif;
    font-size: 28px; color: #3a3d40; letter-spacing: 1px;
  }
  .brand-dot { width: 26px; height: 26px; border-radius: 50%; background: var(--blue); }
  .main-nav {
    position: absolute; left: 440px; top: 0; height: 78px; width: 536px;
    display: flex; border-bottom: 1px solid var(--line); border-radius: 0 0 8px 0;
    border-right: 1px solid var(--line);
  }
  .main-nav a {
    display: flex; align-items: center; justify-content: center;
    border-left: 1px solid var(--line);
    font-family: "Roboto Condensed", Arial, sans-serif;
    font-size: 13px; color: var(--blue); text-decoration: none;
  }
  .main-nav a.is-active { background: var(--blue-pale); position: relative; }
  .main-nav a.is-active::after {
    content: ""; position: absolute; left: 50%; bottom: -6px; width: 10px; height: 10px;
    background: #fff; transform: translateX(-50%) rotate(45deg);
  }
  .hero-frame {
    position: absolute; left: 216px; top: 78px; width: 760px; height: 292px;
    background: var(--frame); border-radius: 8px 0 0 8px;
  }
  .hero {
    position: absolute; left: 224px; top: 87px; width: 752px; height: 275px;
    border-radius: 8px; overflow: hidden;
    background: radial-gradient(ellipse at 40% 50%, var(--board) 0, var(--board-dark) 100%);
  }
  .hero-photo { position: absolute; inset: 0; }
  .hero-dots { position: absolute; left: 9px; top: 8px; display: flex; gap: 7px; }
  .hero-dots span { width: 13px; height: 13px; border-radius: 50%; background: #a9aaa4; }
  .hero-dots span.is-current { background: #fff; }
  .hero-copy {
    position: absolute; left: 422px; top: 18px; color: #fff;
    font-family: "Roboto Condensed", Arial, sans-serif;
    text-shadow: 1px 1px 2px rgba(0,0,0,.6);
  }
  .hero-copy h1 { font-size: 50px; font-weight: 400; line-height: 50px; letter-spacing: -1px; }
  .hero-copy p { font-size: 23px; line-height: 24px; }
  .feature {
    position: absolute; top: 370px; height: 168px;
    border: 1px solid var(--line); border-top: none; border-left: none;
    border-radius: 0 0 8px 0;
  }
  .feature h2 {
    position: absolute; left: 8px; top: 10px;
    font-family: "Roboto Condensed", Arial, sans-serif;
    font-size: 17px; font-weight: 400; color: var(--blue); white-space: nowrap;
  }
  .feature-photo {
    position: absolute; left: 10px; top: 40px; width: 72px; height: 120px;
    border-radius: 6px; border: 2px solid #fff; box-shadow: 0 0 0 1px #cfd6db;
  }
  .feature h3 { position: absolute; left: 99px; top: 42px; font-size: 13px; color: var(--title); }
  .feature p { position: absolute; left: 99px; top: 66px; width: 140px; font-size: 10px; line-height: 17px; }
  .learn-more {
    position: absolute; top: 548px; width: 84px; height: 18px; border-radius: 9px;
    background: linear-gradient(to right, var(--olive) 78%, var(--olive-dark) 78%);
    color: #fff; text-decoration: none;
    font-family: "Roboto Condensed", Arial, sans-serif; font-size: 11px;
    display: flex; align-items: center; padding-left: 9px;
  }
  .learn-more svg { position: absolute; right: 8px; top: 6px; }
  .site-footer {
    position: absolute; left: 0; top: 598px; width: 1200px; text-align: center;
    font-family: "Roboto Condensed", Arial, sans-serif; font-size: 10px; color: #666;
  }
</style>
</head>
<body>
  <div class="sheet"></div>

  <div class="brand"><span class="brand-dot"></span>47Vora</div>

  <nav class="main-nav">
    <a href="#" style="width:56px">HOME</a>
    <a href="#" class="is-active" style="width:69px">COMPANY</a>
    <a href="#" style="width:125px">TECHNICAL SERVICES</a>
    <a href="#" style="width:119px">CREATIVE SERVICES</a>
    <a href="#" style="width:73px">PARTNERS</a>
    <a href="#" style="width:94px">CONTACT US</a>
  </nav>

  <div class="hero-frame"></div>
  <section class="hero">
    <div class="hero-photo" role="img" aria-label="Young boy in glasses and a suit pointing at a chalkboard full of equations"></div>
    <div class="hero-dots"><span></span><span class="is-current"></span><span></span><span></span><span></span><span></span></div>
    <div class="hero-copy">
      <h1>SMART</h1>
      <p>we don't believe in the term<br>"overqualified"</p>
    </div>
  </section>

  <article class="feature" style="left:224px;width:246px">
    <h2>FOR GRAPHIC DESIGNERS</h2>
    <div class="feature-photo" role="img" aria-label="Designer sitting in a cardboard box thinking" style="background:linear-gradient(#2a3034,#0e1012 70%,#b08858)"></div>
    <h3>Get Creative!</h3>
    <p>47Vora is looking for top creative talent to deliver graphic design solutions for some leading global brands Do you have what it takes?</p>
  </article>
  <a class="learn-more" href="#" style="left:378px">LEARN MORE<svg width="5" height="6"><path d="M0 0L5 3L0 6Z" fill="#fff"/></svg></a>

  <article class="feature" style="left:472px;width:257px">
    <h2>FOR CLIENTS</h2>
    <div class="feature-photo" role="img" aria-label="Business team meeting around a table" style="background:linear-gradient(#c9a878,#8a7a6a 60%,#e6e4df)"></div>
    <h3>The 47Vora Difference</h3>
    <p style="width:150px">Smart, Flexible, Thoughtful: find out why leading corporations and government agencies are turning to 47vora to help manage their most demanding IT services challenges.</p>
  </article>
  <a class="learn-more" href="#" style="left:636px">LEARN MORE<svg width="5" height="6"><path d="M0 0L5 3L0 6Z" fill="#fff"/></svg></a>

  <article class="feature" style="left:730px;width:246px">
    <h2>FOR PARTNERS</h2>
    <div class="feature-photo" role="img" aria-label="Business partners shaking hands" style="background:linear-gradient(#8ea0b4,#3d4654 60%,#c9cdd2)"></div>
    <h3>Team Up With the Best</h3>
    <p>When it comes to technology partnerships, our mission it so make you a success.</p>
  </article>
  <a class="learn-more" href="#" style="left:883px">LEARN MORE<svg width="5" height="6"><path d="M0 0L5 3L0 6Z" fill="#fff"/></svg></a>

  <footer class="site-footer">Copyright 2010, 47Vora, LLC All rights reserved.</footer>
</body>
</html>
```